Creative, fresh business card design for Ripplecraft Facades

We need a fresh, creative business card design for Ripplecraft Facades. We are the manufacturer of Ripplecraft Facades in Australia. Wall panels are 2400 x 1200mm panels made from MDF and feature 3D patterns on the face of the panel. The colours to be used are green, silver/grey and white RGB
Red 187
Green 207
Blue 65.

An idea is to possibly use a watermark of one of our designs as a background (like on the "Grids" design on the left hand side of page 2 of our brochure).

Target Market(s)

Interior designers, architects, builders and home renovators

Industry/Entity Type

Business

Contact Information for Business Card

Details to go on the card are:
Our logo (attached),
Slogan: "Decorative panels for interiors and exteriors",
Contact name,
Position,
Mobile phone number,
Business address,
Business phone,
Business fax,
Website and
Email address.

I have attached a few images of our panels and our brochure for reference.

The colours of the business card should feature our logo colours which are: RGB
Red 187
Green 207
Blue 65

Requirements
Must have
• Very modern fonts and design. Some of the designs shown especially the "Prisms" design which is a popular design.
Nice to have
• Creative but simple design. Very contemporary.
Should not have
• Anything ornate or old fashioned.

```html
<!DOCTYPE html>
<html lang="en">
<head>
<meta charset="utf-8">
<title>Ripplecraft Facades – Business Card</title>
<link href="https://fonts.googleapis.com/css2?family=Play:wght@400;700&display=swap" rel="stylesheet">
<style>
  :root {
    --brand-green: rgb(187, 207, 65);
    --panel-grey: #8c8c8c;
    --card-white: #f4f4f4;
    --shade-grey: #dcdcdc;
    --text-white: #ffffff;
    --stage-bg: #e9e9e7;
  }
  html, body {
    margin: 0;
    padding: 0;
    width: 1200px;
    height: 900px;
    overflow: hidden;
    background: var(--stage-bg);
    font-family: "Play", "Arial", sans-serif;
  }
  .stage {
    position: relative;
    width: 1200px;
    height: 900px;
  }
  .card {
    position: absolute;
    box-shadow: 0 6px 18px rgba(0, 0, 0, 0.18);
    overflow: hidden;
  }

  /* Front: contact side */
  .card-front {
    left: 78px;
    top: 35px;
    width: 587px;
    height: 362px;
    background: var(--brand-green);
    color: var(--text-white);
    text-align: center;
  }
  .contact-name {
    position: absolute;
    top: 58px;
    left: 0;
    width: 587px;
    margin: 0;
    font-size: 27px;
    font-weight: 700;
    letter-spacing: 0.5px;
  }
  .contact-role {
    position: absolute;
    top: 86px;
    left: 0;
    width: 587px;
    margin: 0;
    font-size: 17px;
    font-weight: 700;
  }
  .contact-lines {
    position: absolute;
    top: 130px;
    left: 0;
    width: 587px;
    margin: 0;
    padding: 0;
    list-style: none;
    font-size: 17px;
    font-weight: 700;
    line-height: 26.5px;
  }
  .contact-address {
    position: absolute;
    top: 257px;
    left: 0;
    width: 587px;
    margin: 0;
    font-size: 17px;
    font-weight: 700;
    line-height: 23px;
    font-style: normal;
  }

  /* Back: brand side */
  .card-back {
    left: 388px;
    top: 505px;
    width: 567px;
    height: 352px;
    background: linear-gradient(90deg, var(--card-white) 0%, #ededed 100%);
  }
  .panel-texture {
    position: absolute;
    right: 0;
    top: 0;
    width: 250px;
    height: 352px;
    background: linear-gradient(90deg, rgba(220,220,220,0) 0%, var(--shade-grey) 45%, #e8e8e8 75%, #d4d4d4 100%);
  }
  .brand-name {
    position: absolute;
    left: 171px;
    top: 150px;
    display: flex;
    align-items: center;
    gap: 10px;
    margin: 0;
    font-size: 25px;
    font-weight: 700;
    color: var(--panel-grey);
    white-space: nowrap;
  }
  .brand-square {
    width: 22px;
    height: 22px;
    background: var(--brand-green);
  }
  .slogan {
    position: absolute;
    left: 0;
    top: 239px;
    width: 567px;
    margin: 0;
    padding-left: 171px;
    box-sizing: border-box;
    width: 396px;
    left: 0;
    text-align: center;
    font-size: 15px;
    letter-spacing: 2.2px;
    line-height: 19px;
    color: var(--panel-grey);
  }
  .website {
    position: absolute;
    left: 171px;
    top: 302px;
    width: 225px;
    margin: 0;
    text-align: center;
    font-size: 16px;
    font-weight: 700;
    color: var(--brand-green);
  }
</style>
</head>
<body>
<main class="stage">
  <section class="card card-front" aria-label="Business card contact side">
    <h1 class="contact-name">MARCUS HALE</h1>
    <p class="contact-role">Managing Director</p>
    <ul class="contact-lines">
      <li>P: (044) 555 018 204</li>
      <li>M:&nbsp; (044)555018377</li>
      <li>F: (044) 555 018 204</li>
      <li>E:&nbsp; hello@ripplecraft.com</li>
    </ul>
    <address class="contact-address">48, Tanner Lane Works<br>Victoria, 3170.</address>
  </section>

  <section class="card card-back" aria-label="Business card brand side">
    <div class="panel-texture" role="img" aria-label="Faint relief pattern of a white 3D wall panel"></div>
    <p class="brand-name"><span class="brand-square"></span>Ripplecraft Facades</p>
    <p class="slogan">decorative panels for<br>interiors &amp; landscapes</p>
    <p class="website">www.ripplecraft.com</p>
  </section>
</main>
</body>
</html>
```